Design a website for a newly developed Delta 8 THC Company

Design a responsive Website with the following goals in mind:
- Built on Wordpress/WooCommerce theme. Please use this when designing for ease of integration.
- Build trust with website visitors with an engaging, informative content driven website, that leads to a conversion of product purchase and repeat business. We will also be driving consumers to businesses that carry our products as well.
- The website will embody a lifestyle feel and make the visitor identify with the content.
- The website will allow for super charged SEO and other digital marketing and advertising strategies and tactics used to increase discovery, awareness, and conversion.
Please see additional goals in the uploaded files.
Target Market(s)
Male/Female 21-
Industry/Entity Type
Cannabis/Hemp
Coding
Coded - Design and coding required
Number of Pages Required
5+ page
Font styles to use
Other font styles liked:
- Montserrat
Look and feel
Each slider illustrates characteristics of the customer's brand and the style your logo design should communicate.

```html
<!DOCTYPE html>
<html lang="en">
<head>
<meta charset="utf-8">
<title>AURELO – Delta 8 THC</title>
<link href="https://fonts.googleapis.com/css2?family=Montserrat:wght@400;500;600;700;800&family=Lato:ital,wght@0,400;0,700;1,400&display=swap" rel="stylesheet">
<style>
:root{
  --bg:#0b0b0b;
  --bg-soft:#111111;
  --panel:#141414;
  --gold:#c7a25a;
  --gold-light:#e0c48a;
  --gold-dark:#8c6b2f;
  --white:#ffffff;
  --muted:#d8d8d8;
  --leaf:#2f5a2a;
  --leaf-dark:#16301a;
}
*{box-sizing:border-box;margin:0;padding:0}
html,body{width:1200px;height:4882px;overflow:hidden}
body{background:var(--bg);color:var(--white);font-family:"Montserrat",sans-serif;position:relative}
.abs{position:absolute}
.btn{position:absolute;display:flex;align-items:center;justify-content:center;border-radius:24px;
  background:linear-gradient(180deg,var(--gold-light),var(--gold) 50%,var(--gold-dark));
  color:var(--white);font-weight:600;font-size:16px;text-transform:uppercase;letter-spacing:.3px}
.ph{position:absolute}

/* header */
.site-header{position:absolute;left:0;top:0;width:1200px;height:112px;background:#050505}
.topbar{position:absolute;left:312px;top:0;width:888px;height:49px;
  background:linear-gradient(90deg,var(--gold-dark),var(--gold) 40%,var(--gold-light));
  clip-path:polygon(0 0,100% 0,100% 100%,40px 100%)}
.topbar .phone{position:absolute;left:352px;top:14px;font-size:15px;font-weight:600;display:flex;gap:8px;align-items:center}
.topbar .social{position:absolute;top:8px;width:32px;height:32px;border:2px solid var(--white);border-radius:50%}
.topbar svg.ic{position:absolute;top:12px}
.brand{position:absolute;left:114px;top:10px;width:80px;text-align:center}
.brand .mark{width:56px;height:56px;border:2px solid var(--gold);border-radius:50%;margin:0 auto 6px}
.brand .name{font-size:14px;letter-spacing:6px;color:var(--gold);font-weight:500}
.main-nav{position:absolute;top:74px;left:0;font-size:15px;font-weight:600}
.main-nav span{position:absolute;white-space:nowrap}

/* hero */
.hero{position:absolute;left:0;top:112px;width:1200px;height:601px;
  background:linear-gradient(100deg,#0c0f0c 0%,#101a10 35%,#24472a 60%,#3b6b35 75%,#1c3a1f 100%)}
.hero h1{position:absolute;left:106px;top:168px;font-size:78px;font-weight:800;letter-spacing:1px;line-height:1}
.hero p{position:absolute;left:112px;top:250px;width:440px;font-size:16.5px;line-height:28px;font-family:"Lato",sans-serif}
.arrow{position:absolute;top:282px;width:36px;height:36px;border:2px solid #bbb;border-radius:50%}
.dots{position:absolute;top:554px;left:502px;display:flex;gap:12px}
.dots i{display:block;width:40px;height:3px;background:#555}
.dots i:first-child{background:var(--white)}

/* about */
.about{position:absolute;left:0;top:713px;width:1200px;height:500px;background:var(--bg-soft)}
.about .emblem{position:absolute;left:170px;top:105px;width:310px;height:310px;border:3px solid var(--gold);border-radius:50%;
  display:flex;align-items:center;justify-content:center;font-size:38px;font-weight:700;letter-spacing:10px;color:var(--gold)}
.h2{font-size:40px;font-weight:700;text-transform:uppercase;line-height:1}
.about h2{position:absolute;left:597px;top:98px}
.about p{position:absolute;left:598px;top:150px;width:460px;font-family:"Lato",sans-serif;font-size:16px;line-height:28.4px}

.gallery{position:absolute;top:1213px;left:0;width:1200px;height:323px;display:flex;gap:2px}
.gallery div{flex:1}

/* products */
.section-title{position:absolute;left:0;width:1200px;text-align:center}
.section-sub{position:absolute;left:0;width:1200px;text-align:center;font-family:"Lato",sans-serif;font-size:18px;line-height:29px}
.products{position:absolute;left:112px;top:1778px;width:976px;display:grid;grid-template-columns:repeat(4,229px);column-gap:20px;row-gap:22px}
.card{height:291px;border:2px solid var(--gold-dark);background:var(--panel);position:relative;text-align:center}
.card .pic{position:absolute;left:38px;top:18px;width:150px;height:150px;border-radius:8px;
  background:linear-gradient(180deg,#2a2a2a,#0a0a0a)}
.card .pic.tall{left:86px;width:56px;border-radius:2px}
.card h3{position:absolute;top:194px;width:100%;font-size:19px;font-weight:600}
.card .price{position:absolute;top:224px;width:100%;font-size:16px;font-weight:600}
.card .opt{position:absolute;top:252px;width:100%;font-size:13px;font-weight:600;color:var(--gold)}

/* banner */
.standard{position:absolute;left:0;top:2465px;width:1200px;height:417px;
  background:linear-gradient(90deg,#2d4a22 0%,#5e7042 35%,#6e6e6a 55%,#2d2f2b 80%,#1d1f1c 100%)}
.standard h2{position:absolute;left:641px;top:92px;font-size:28px;font-weight:700}
.standard p{position:absolute;left:641px;top:142px;width:460px;font-family:"Lato",sans-serif;font-size:16.5px;line-height:30px}

/* testimonials */
.quotes{position:absolute;top:3094px;left:114px;display:flex;gap:22px}
.quote{width:309px;height:279px;border:2px solid var(--gold-dark);text-align:center;position:relative}
.quote .qm{position:absolute;top:12px;width:100%;font-size:58px;color:var(--gold);font-family:Georgia,serif;font-weight:700;line-height:1}
.quote p{position:absolute;top:72px;left:14px;right:14px;font-family:"Lato",sans-serif;font-style:italic;font-size:14px;line-height:26px}
.quote .stars{position:absolute;top:216px;width:100%;display:flex;justify-content:center;gap:2px}
.quote .who{position:absolute;top:243px;width:100%;font-size:16px;font-weight:500}

/* blog */
.post-date{position:absolute;font-family:"Lato",sans-serif;font-style:italic;font-size:13.5px;display:flex;gap:6px;align-items:center}
.post-title{position:absolute;font-size:15.5px;line-height:29px}

/* newsletter */
.newsletter{position:absolute;left:0;top:4253px;width:1200px;height:307px;
  background:linear-gradient(90deg,#3a2210 0%,#4a5a28 25%,#1f3b1f 55%,#2b4a2b 80%,#142814 100%)}
.newsletter h2{position:absolute;left:0;width:1200px;text-align:center;top:82px;font-size:31px;font-weight:700}
.newsletter p{position:absolute;left:0;width:1200px;text-align:center;top:128px;font-family:"Lato",sans-serif;font-size:14px}
.signup-input{position:absolute;left:328px;top:176px;width:413px;height:47px;background:var(--white);color:#666;font-size:14px;padding:15px 20px;font-family:"Lato",sans-serif}
.signup-btn{position:absolute;left:741px;top:176px;width:131px;height:47px;background:linear-gradient(180deg,var(--gold),var(--gold-dark));
  font-weight:700;font-size:15px;display:flex;align-items:center;justify-content:center}

/* footer */
.footer h4{position:absolute;top:4622px;font-size:16.5px;font-weight:600}
.footer ul{position:absolute;list-style:none;font-size:14px;line-height:25.5px}
.footer .contact{position:absolute;font-size:14px;line-height:20px;display:flex;gap:12px}
.footer .circ{position:absolute;top:4665px;width:32px;height:32px;border-radius:50%;background:var(--gold)}
.footer .rule{position:absolute;left:112px;top:4821px;width:976px;height:1px;background:#444}
.footer .legal{position:absolute;top:4843px;font-size:14px}
</style>
</head>
<body>

<header class="site-header">
  <div class="topbar">
    <div class="phone">
      <svg width="14" height="14" viewBox="0 0 24 24"><path fill="#fff" d="M6.6 10.8a15 15 0 0 0 6.6 6.6l2.2-2.2a1 1 0 0 1 1-.25 11.4 11.4 0 0 0 3.6.57 1 1 0 0 1 1 1V20a1 1 0 0 1-1 1A17 17 0 0 1 3 4a1 1 0 0 1 1-1h3.5a1 1 0 0 1 1 1c0 1.25.2 2.45.57 3.6a1 1 0 0 1-.25 1z"/></svg>
      888 - 888 - 8888
    </div>
    <span class="social" style="left:523px"></span>
    <span class="social" style="left:565px"></span>
    <span class="social" style="left:607px"></span>
    <svg class="ic" style="left:662px" width="24" height="24" viewBox="0 0 24 24"><circle cx="10" cy="10" r="7" fill="none" stroke="#fff" stroke-width="2"/><path d="M15 15l6 6" stroke="#fff" stroke-width="2"/></svg>
    <svg class="ic" style="left:700px" width="24" height="24" viewBox="0 0 24 24"><circle cx="12" cy="12" r="10" fill="none" stroke="#fff" stroke-width="2"/><circle cx="12" cy="10" r="3.5" fill="none" stroke="#fff" stroke-width="2"/><path d="M6 19c2-4 10-4 12 0" fill="none" stroke="#fff" stroke-width="2"/></svg>
    <svg class="ic" style="left:740px" width="26" height="24" viewBox="0 0 26 24"><path d="M1 3h4l3 12h13l3-9H7" fill="none" stroke="#fff" stroke-width="2"/><circle cx="10" cy="20" r="2" fill="#fff"/><circle cx="19" cy="20" r="2" fill="#fff"/></svg>
  </div>
  <div class="brand"><div class="mark"></div><div class="name">AURELO</div></div>
  <nav class="main-nav">
    <span style="left:401px">HOME</span>
    <span style="left:498px">ABOUT US</span>
    <span style="left:628px">SERVICES</span>
    <span style="left:754px">PRODUCTS</span>
    <span style="left:891px">BLOG</span>
    <span style="left:983px">CONTACT US</span>
  </nav>
</header>

<section class="hero" role="img" aria-label="Close-up of green hemp leaves on a dark background">
  <h1>AURELO</h1>
  <p>Lorem ipsum dolor sit amet, consectetur adipiscing elit, sed do eiusmod tempor incididunt ut labore et dolore magna aliqua.</p>
  <span class="btn" style="left:114px;top:358px;width:176px;height:46px">Get Started</span>
  <span class="arrow" style="left:65px"><svg width="32" height="32" viewBox="0 0 32 32"><path d="M19 9l-7 7 7 7" fill="none" stroke="#ddd" stroke-width="2"/></svg></span>
  <span class="arrow" style="left:1102px"><svg width="32" height="32" viewBox="0 0 32 32"><path d="M13 9l7 7-7 7" fill="none" stroke="#ddd" stroke-width="2"/></svg></span>
  <div class="dots"><i></i><i></i><i></i><i></i></div>
</section>

<section class="about">
  <div class="emblem">AURELO</div>
  <h2 class="h2">About Us</h2>
  <p>Lorem ipsum dolor sit amtur adcing eit, eiusmod tempor incididunt ut labore et dolore a. Quis ipsum suspendisse ultrices gravida. Risus commodo via maecenas accumsan lacus vel facilisis. Lorem ipsuor sit am, consectetur adcing eit, eiusmod tempor incididunt ut lre et e magna aliqua. Quis ipsum suspendisse ultrices gravida. Risus commodo viverra maecenas accumsan lacus vel facilisis.</p>
  <span class="btn" style="left:599px;top:371px;width:176px;height:48px">Learn More</span>
</section>

<div class="gallery">
  <div role="img" aria-label="Scientist in goggles inspecting hemp plants" style="background:linear-gradient(135deg,#d8dad8,#6f8c56 55%,#2d5a22)"></div>
  <div role="img" aria-label="Rows of young hemp plants in pots in a greenhouse" style="background:linear-gradient(180deg,#9fbf6a,#5b7a33 45%,#3a2a1c)"></div>
  <div role="img" aria-label="Smiling woman holding hemp in a field" style="background:linear-gradient(135deg,#c9d4b8,#8aa46a 50%,#4d6a33)"></div>
</div>

<h2 class="h2 section-title" style="top:1620px">Featured Products</h2>
<p class="section-sub" style="top:1673px">Lorem ipsum dolor sit amet, consectetur adipiscing elit, sed do eiusmod<br>tempor int ut labore et dolore magna aliqua.</p>

<div class="products">
  <div class="card"><div class="pic" role="img" aria-label="Jar of delta-8 gummies"></div><h3>Product Name</h3><div class="price">From: $39.99</div><div class="opt">SELECT OPTIONS ›</div></div>
  <div class="card"><div class="pic" role="img" aria-label="Jar of delta-8 gummies"></div><h3>Product Name</h3><div class="price">From: $39.99</div><div class="opt">SELECT OPTIONS ›</div></div>
  <div class="card"><div class="pic" role="img" aria-label="Jar of delta-8 gummies"></div><h3>Product Name</h3><div class="price">From: $39.99</div><div class="opt">SELECT OPTIONS ›</div></div>
  <div class="card"><div class="pic" role="img" aria-label="Jar of delta-8 gummies"></div><h3>Product Name</h3><div class="price">From: $39.99</div><div class="opt">SELECT OPTIONS ›</div></div>
  <div class="card"><div class="pic" role="img" aria-label="Jar of delta-8 gummies"></div><h3>Product Name</h3><div class="price">From: $39.99</div><div class="opt">SELECT OPTIONS ›</div></div>
  <div class="card"><div class="pic tall" role="img" aria-label="Slim black product box" style="top:18px"></div><h3>Product Name</h3><div class="price">From: $39.99</div><div class="opt">SELECT OPTIONS ›</div></div>
  <div class="card"><div class="pic tall" role="img" aria-label="Slim black product box"></div><h3>Product Name</h3><div class="price">From: $39.99</div><div class="opt">SELECT OPTIONS ›</div></div>
  <div class="card"><div class="pic tall" role="img" aria-label="Slim black product box"></div><h3>Product Name</h3><div class="price">From: $39.99</div><div class="opt">SELECT OPTIONS ›</div></div>
</div>

<section class="standard" role="img" aria-label="Woman in a straw hat holding a hemp leaf in a field">
  <h2>THE STANDARD LOREM IPSUM</h2>
  <p>Lorem ipsum dolor sit amet, consectetadipiscing elit, sed do eiusmod tempor int ut labore et dolore magna aliqua. Quis ipsum suspendisse ultrices gravida. Risus commodo viverra maecenan lacus vel facilisis.</p>
  <span class="btn" style="left:643px;top:284px;width:186px;height:46px">Learn More</span>
</section>

<h2 class="h2 section-title" style="top:2950px">What Our Clients Say</h2>
<p class="section-sub" style="top:3002px">Lorem ipsum dolor sit amet, consectetur adipiscing elit, sed do eiusmod tempor int ut<br>labore et dolore magna aliqua. Quis ipsum suspendisse ultrices gravida. Risus commodo viverra</p>

<div class="quotes">
  <div class="quote"><div class="qm">“</div><p>Lorem ipsum dolor sit amet, consectetur adipiscing elit, sed do eiusmod t incididunt ut labore et dolore magna aliqua. Quis ipsum suspendisse ultrices gravida. Risu modo viverra maecenas</p><div class="stars"><svg width="74" height="14" viewBox="0 0 74 14"><g fill="#d8a93a"><path id="st" d="M7 0l2 4.5 5 .5-3.8 3.3 1.1 5L7 10.7 2.7 13.3l1.1-5L0 5l5-.5z"/><use href="#st" x="15"/><use href="#st" x="30"/><use href="#st" x="45"/><use href="#st" x="60"/></g></svg></div><div class="who">- James Smith</div></div>
  <div class="quote"><div class="qm">“</div><p>Lorem ipsum dolor sit amet, consectetur adipiscing elit, sed do eiusmod t incididunt ut labore et dolore magna aliqua. Quis ipsum suspendisse ultrices gravida. Risu modo viverra maecenas</p><div class="stars"><svg width="74" height="14" viewBox="0 0 74 14"><g fill="#d8a93a"><use href="#st"/><use href="#st" x="15"/><use href="#st" x="30"/><use href="#st" x="45"/><use href="#st" x="60"/></g></svg></div><div class="who">- James Smith</div></div>
  <div class="quote"><div class="qm">“</div><p>Lorem ipsum dolor sit amet, consectetur adipiscing elit, sed do eiusmod t incididunt ut labore et dolore magna aliqua. Quis ipsum suspendisse ultrices gravida. Risu modo viverra maecenas</p><div class="stars"><svg width="74" height="14" viewBox="0 0 74 14"><g fill="#d8a93a"><use href="#st"/><use href="#st" x="15"/><use href="#st" x="30"/><use href="#st" x="45"/><use href="#st" x="60"/></g></svg></div><div class="who">- James Smith</div></div>
</div>

<h2 class="h2 section-title" style="top:3525px">Our Latest Blog</h2>
<p class="section-sub" style="top:3577px">Lorem ipsum dolor sit amet, consectetur adipiscing elit, sed do eiusmod tempor int ut<br>labore et dolore magna aliqua. Quis ipsum suspendisse ultrices gravida. Risus commodo viverra</p>

<svg width="0" height="0" style="position:absolute"><defs><g id="cal"><rect x="1" y="2.5" width="12" height="10.5" fill="none" stroke="#fff" stroke-width="1.4"/><path d="M1 6h12M4 0v4M10 0v4" stroke="#fff" stroke-width="1.4"/></g></defs></svg>

<div class="ph" role="img" aria-label="Hands rolling dried hemp on a table" style="left:112px;top:3659px;width:472px;height:294px;background:linear-gradient(135deg,#6b5a4a,#c9c4bc 45%,#8a7866)"></div>
<div class="post-date" style="left:112px;top:3978px"><svg width="14" height="14"><use href="#cal"/></svg>15 April,2021</div>
<div class="abs" style="left:112px;top:4016px;width:470px;font-size:19.5px;line-height:29px;font-weight:500">Lorem ipsum dolor simet, consectetr adipiscing elit, sed do eiusmod tempor</div>
<div class="abs" style="left:112px;top:4080px;width:470px;font-family:'Lato',sans-serif;font-size:13.5px;line-height:25px">Lorem ipsum dolor sit amet, consectetur adipiscineiusmod tempor incididunt ut labore et dolore magna aliqua. Quis ipsum pendisse ultrices gravida.</div>

<div class="ph" role="img" aria-label="Two researchers examining hemp plants" style="left:601px;top:3659px;width:237px;height:148px;background:linear-gradient(135deg,#3d6a2a,#b9b7a8 50%,#2b4a1e)"></div>
<div class="post-date" style="left:601px;top:3819px"><svg width="14" height="14"><use href="#cal"/></svg>15 April,2020</div>
<div class="post-title" style="left:601px;top:3847px;width:240px">Lorem ipsum dolorcoectetur adipiscing elit, sed do</div>

<div class="ph" role="img" aria-label="Bottles of hemp oil with seeds and leaves" style="left:851px;top:3659px;width:239px;height:148px;background:linear-gradient(135deg,#4e7a2c,#c9a846 50%,#6b5a3a)"></div>
<div class="post-date" style="left:851px;top:3819px"><svg width="14" height="14"><use href="#cal"/></svg>15 April,2021</div>
<div class="post-title" style="left:851px;top:3847px;width:240px">Lorem ipsum dolorcoectetur adipiscing elit, sed do</div>

<div class="ph" role="img" aria-label="Hand holding a hemp leaf among plants" style="left:601px;top:3921px;width:237px;height:148px;background:linear-gradient(135deg,#1c3a16,#4f8a34 50%,#23461c)"></div>
<div class="post-date" style="left:601px;top:4081px"><svg width="14" height="14"><use href="#cal"/></svg>15 April,2020</div>
<div class="post-title" style="left:601px;top:4108px;width:240px">Lorem ipsum dolorcoectetur adipiscing elit, sed do</div>

<div class="ph" role="img" aria-label="Gloved hand holding a vial of oil beside hemp" style="left:851px;top:3921px;width:239px;height:148px;background:linear-gradient(135deg,#2f5a22,#d8dce4 55%,#5a6fa0)"></div>
<div class="post-date" style="left:851px;top:4081px"><svg width="14" height="14"><use href="#cal"/></svg>15 April,2020</div>
<div class="post-title" style="left:851px;top:4108px;width:240px">Lorem ipsum dolorcoectetur adipiscing elit, sed do</div>

<section class="newsletter" role="img" aria-label="Hemp plants in warm evening light">
  <h2>WE WANT TO STAY CONNECTED WITH YOU.</h2>
  <p>Sed ut perspiciatis unde omnis iste natus error sit voluptatem accusantium</p>
  <div class="signup-input">Enter Your Email</div>
  <div class="signup-btn">SUBSCRIBE</div>
</section>

<footer class="footer">
  <div class="abs" style="left:168px;top:4614px;width:120px;text-align:center">
    <div style="width:110px;height:110px;border:2px solid var(--gold);border-radius:50%;margin:0 auto 10px"></div>
    <div style="font-size:24px;letter-spacing:8px;color:var(--gold);font-weight:500">AURELO</div>
  </div>
  <h4 style="left:459px">QUICK LINKS</h4>
  <ul style="left:459px;top:4656px"><li>Home</li><li>About Us</li><li>Services</li><li>products</li><li>Blog</li><li>Contact US</li></ul>
  <h4 style="left:662px">CONTACTS INFO</h4>
  <div class="contact" style="left:662px;top:4660px"><svg width="12" height="16" viewBox="0 0 12 16"><path d="M6 0a6 6 0 0 1 6 6c0 4-6 10-6 10S0 10 0 6a6 6 0 0 1 6-6z" fill="#fff"/><circle cx="6" cy="6" r="2.2" fill="#0b0b0b"/></svg><span>123 Avenue name, City name<br>10150, United States</span></div>
  <div class="contact" style="left:658px;top:4716px"><svg width="14" height="14" viewBox="0 0 24 24"><path fill="#fff" d="M6.6 10.8a15 15 0 0 0 6.6 6.6l2.2-2.2a1 1 0 0 1 1-.25 11.4 11.4 0 0 0 3.6.57 1 1 0 0 1 1 1V20a1 1 0 0 1-1 1A17 17 0 0 1 3 4a1 1 0 0 1 1-1h3.5a1 1 0 0 1 1 1c0 1.25.2 2.45.57 3.6a1 1 0 0 1-.25 1z"/></svg><span>888 888 8888</span></div>
  <div class="contact" style="left:658px;top:4752px"><svg width="14" height="12" viewBox="0 0 14 12"><rect width="14" height="12" fill="#fff"/><path d="M0 0l7 6 7-6" fill="none" stroke="#0b0b0b" stroke-width="1.4"/></svg><span>info@aurelo.com</span></div>
  <h4 style="left:935px">STAT CONECTED</h4>
  <span class="circ" style="left:929px"></span>
  <span class="circ" style="left:971px"></span>
  <span class="circ" style="left:1013px"></span>
  <span class="circ" style="left:1055px"></span>
  <div class="rule"></div>
  <div class="legal" style="left:112px">Copyright © 2021 AURELO. All Rights Reserved.</div>
  <div class="legal" style="left:664px">Terms &amp; Conditions</div>
  <div class="legal" style="left:823px">Privacy Policy</div>
  <div class="legal" style="left:943px">About Us</div>
  <div class="legal" style="left:1032px">Support</div>
</footer>

</body>
</html>
```